Business Card Design for my Real Estate Investing Company

This is for a Real Estate Investing Company that will be serving the Las Vegas Valley. Id like the following slogan included: "Investing in Our Community" I have attached my logo. You will see the color tones I'm interested in..in my logo. I would like the card to be double-sided with a modern, professional look.
Target Market(s)
Homeowners, banks, real estate industry
Industry/Entity Type
Real Estate
Contact Information for Business Card
name: Dale Harwick
position: Managing Member
address: 4821 Corliss Pkwy ste 207-300
N. Las Vegas, NV 89084
phone: (702) 555-0143
fax: (702) 555-0187
email: SummitRidgeEstate@hollowmail.test
web: SummitRidgeEstates.test
*At the bottom of the card I would like....
We buy houses for cash....no repairs, no commissions, no fees!
Logo Text
SUMMIT RIDGE ESTATES "Investing in Our Community"
Font styles to use
Other font styles liked:
- Lora
Requirements
Must have
- On the back of the card, i'd like to have my logo large and the following statements:
- Are you considering selling your home? Want a simple, hassle-free transaction? We can help! We buy houses for cash and can close quickly! No need to do any repairs, no realtor commissions, no closing costs.....and no headaches. Let us help you with your real estate needs...!
Nice to have
- multiple colors 2 two tone on front and back

```html
<!DOCTYPE html>
<html lang="en">
<head>
<meta charset="utf-8">
<title>Summit Ridge Estates – Business Card</title>
<link href="https://fonts.googleapis.com/css2?family=Lora:wght@400;600&family=Montserrat:wght@400;500&family=Oswald:wght@500&display=swap" rel="stylesheet">
<style>
  :root {
    --backdrop: #2b2b2d;
    --card: #050505;
    --blue: #1a5bb5;
    --white: #ffffff;
    --paper: #f4f4f4;
    --grey: #9a9a9a;
  }
  * { margin: 0; padding: 0; box-sizing: border-box; }
  html, body { width: 1200px; height: 900px; overflow: hidden; }
  body { background: var(--backdrop); position: relative; font-family: "Montserrat", sans-serif; }

  .card {
    position: absolute;
    width: 620px; height: 354px;
    background: var(--card);
    border-radius: 18px;
    overflow: hidden;
    color: var(--white);
    box-shadow: 0 12px 30px rgba(0,0,0,.45);
  }
  .card--back { left: 90px; top: 70px; }
  .card--front { left: 490px; top: 476px; }

  /* back */
  .back-brand {
    position: absolute; top: 46px; left: 0; right: 0;
    display: flex; justify-content: center; align-items: center; gap: 14px;
  }
  .back-brand__mark { width: 26px; height: 26px; background: var(--grey); }
  .back-brand__name {
    font-family: "Lora", serif; font-weight: 600; font-size: 38px;
    color: var(--blue); letter-spacing: 1px;
  }
  .back-pitch {
    position: absolute; top: 146px; left: 40px; right: 40px;
    text-align: center; font-size: 14.5px; line-height: 1.45;
  }
  .back-tagline {
    position: absolute; bottom: 36px; left: 0; right: 0; text-align: center;
    font-family: "Oswald", sans-serif; font-weight: 500; font-size: 16px;
    color: var(--blue); letter-spacing: .5px;
  }

  /* front */
  .front-brand { position: absolute; top: 42px; left: 36px; }
  .front-brand__row { display: flex; align-items: center; gap: 10px; }
  .front-brand__mark { width: 18px; height: 18px; background: var(--grey); }
  .front-brand__name {
    font-family: "Lora", serif; font-weight: 600; font-size: 27px;
    color: var(--blue); letter-spacing: .5px;
  }
  .front-brand__slogan {
    margin-top: 4px; margin-left: 28px;
    font-family: "Lora", serif; font-size: 12px; color: var(--white); letter-spacing: 2.5px;
  }
  .holder { position: absolute; top: 40px; right: 34px; text-align: right; }
  .holder__name {
    font-family: "Lora", serif; font-size: 22px; color: var(--blue); letter-spacing: 1px;
  }
  .holder__role { font-size: 13px; margin-top: 2px; }
  .holder__rule { margin-top: 6px; margin-left: auto; width: 220px; height: 2px; background: var(--blue); }

  .contact {
    position: absolute; left: 36px; top: 168px; width: 360px;
    border-top: 2px solid var(--blue); padding-top: 10px;
    font-size: 13.5px; line-height: 1.42;
  }
  .contact__address { margin-bottom: 4px; }
  .contact__line { display: flex; align-items: center; gap: 10px; }
  .contact__icon { width: 12px; height: 12px; flex: none; }
  .contact__web span { color: var(--blue); }

  .accent-band {
    position: absolute; right: 0; bottom: 0; width: 190px; height: 150px;
    background: var(--blue);
  }
  .paper-strip {
    position: absolute; left: 0; bottom: 0; width: 430px; height: 16px;
    background: var(--paper);
  }
</style>
</head>
<body>

<section class="card card--back" aria-label="Card back">
  <div class="back-brand">
    <span class="back-brand__mark"></span>
    <span class="back-brand__name">SUMMIT RIDGE ESTATES</span>
  </div>
  <p class="back-pitch">
    Are you considering selling your home?<br>
    Want a simple, hassle-free transaction?<br>
    We can help! We buy houses for cash and can close quickly!<br>
    No need to do any repairs, no realtor commissions, no closing costs<br>
    and no headaches. Let us help you with your real estate needs...!
  </p>
  <p class="back-tagline">WE BUY HOUSES FOR CASH....NO REPAIRS, NO COMMISSIONS, NO FEES!</p>
</section>

<section class="card card--front" aria-label="Card front">
  <div class="front-brand">
    <div class="front-brand__row">
      <span class="front-brand__mark"></span>
      <span class="front-brand__name">SUMMIT RIDGE ESTATES</span>
    </div>
    <p class="front-brand__slogan">"Investing in Our Community"</p>
  </div>

  <div class="holder">
    <p class="holder__name">DALE HARWICK</p>
    <p class="holder__role">Managing Member</p>
    <div class="holder__rule"></div>
  </div>

  <div class="contact">
    <p class="contact__address">4821 Corliss Pkwy ste 207-300<br>N. Las Vegas, NV 89084</p>
    <p class="contact__line">
      <svg class="contact__icon" viewBox="0 0 24 24"><path fill="#1a5bb5" d="M6.6 10.8a15 15 0 0 0 6.6 6.6l2.2-2.2c.3-.3.7-.4 1-.2 1.1.4 2.3.6 3.6.6.6 0 1 .4 1 1V20c0 .6-.4 1-1 1A17 17 0 0 1 3 4c0-.6.4-1 1-1h3.5c.6 0 1 .4 1 1 0 1.3.2 2.5.6 3.6.1.3 0 .7-.2 1z"/></svg>
      (702) 555-0143
    </p>
    <p class="contact__line">
      <svg class="contact__icon" viewBox="0 0 24 24"><path fill="#1a5bb5" d="M6 3h10v5H6zM4 9h16a2 2 0 0 1 2 2v7h-4v3H6v-3H2v-7a2 2 0 0 1 2-2zm4 7v3h8v-3z"/></svg>
      (702) 555-0187
    </p>
    <p class="contact__line">
      <svg class="contact__icon" viewBox="0 0 24 24"><path fill="#1a5bb5" d="M2 5h20v14H2zm2 2v.5l8 5 8-5V7z"/></svg>
      SummitRidgeEstate@hollowmail.test
    </p>
    <p class="contact__line contact__web">
      <svg class="contact__icon" viewBox="0 0 24 24"><circle cx="12" cy="12" r="9" fill="none" stroke="#1a5bb5" stroke-width="2.5"/><path d="M3 12h18M12 3c3 3 3 15 0 18M12 3c-3 3-3 15 0 18" fill="none" stroke="#1a5bb5" stroke-width="2"/></svg>
      www.<span>SummitRidgeEstates.test</span>
    </p>
  </div>

  <div class="accent-band"></div>
  <div class="paper-strip"></div>
</section>

</body>
</html>
```